Modern Label for cleaning products for the brand Vorlix

We need a label design for our line of cleaning products. The label should feature our logo and an image to identify the product's intended use. I've added our logo and an image for use. This only concerns the design of the label on the front of the bottle.

Label dimensions:
Label 1 (500ml bottle with spray): width 58mm x height 115mm
Label 2: (1L bottle): width 73mm x height 140mm
The design must be consistent for both bottles which you find in the pictures.

The bottles to be labeled are white. See the attachment for a photo of the bottles.

The photo must also appear on the label to identify the product's intended use.

Product information:
Brand: Vorlix
Product: Sanitary Cleaner

This text must be placed on the label:
"Cleans, descales & freshens. followed with this text: "Ideal for quick and powerful cleaning. A ready-to-use product for everyday use."

- Mention the seperate USP's: Sanitary, Bathroom, Toilet, Wet areas

Appearance: This is a consumer product, but it must have a professional appearance. We would like to see a design that use the color blue from our logo.

Target Market(s)

Consumers who take care of their homes and want to maintain it the correct (professional) way

Font styles to use
Sans Serif

Colors
0054AA
0677BA
7BADD7
CADEEF
E8F1F8

Requirements
Must have
• USP's + use of image and logo + blend in 1 design
Nice to have
• Keep the color of the logo in the design
Should not have
• Comic sans

```html
<!DOCTYPE html>
<html lang="en">
<head>
<meta charset="utf-8">
<title>Vorlix Sanitary Cleaner Label</title>
<link href="https://fonts.googleapis.com/css2?family=Lexend:wght@300;400;600;700;800&display=swap" rel="stylesheet">
<style>
  :root {
    --blue-deep: #0054AA;
    --blue-brand: #0677BA;
    --blue-title: #1288b5;
    --blue-soft: #7BADD7;
    --blue-pale: #CADEEF;
    --blue-mist: #E8F1F8;
    --navy-text: #1c4e7a;
    --frame-grey: #e4e6e8;
    --white: #ffffff;
  }
  html, body { margin: 0; padding: 0; }
  body {
    width: 1200px; height: 898px; overflow: hidden;
    background: var(--white);
    font-family: 'Lexend', sans-serif;
    position: relative;
  }
  .label {
    position: absolute; left: 425px; top: 100px;
    width: 356px; height: 701px;
    border-radius: 24px;
    background: linear-gradient(180deg, var(--frame-grey) 0%, var(--frame-grey) 55%, #8fa9c2 75%, #2a6fb5 100%);
    box-shadow: 0 1px 4px rgba(0,0,0,0.15);
  }
  .label-face {
    position: absolute; inset: 8px;
    border-radius: 17px;
    overflow: hidden;
    background: var(--white);
  }
  .face-content { position: absolute; left: -8px; top: -8px; width: 356px; height: 701px; }
  .bg-ring {
    position: absolute; left: 77px; top: 99px;
    width: 316px; height: 316px; border-radius: 50%;
    border: 34px solid var(--blue-mist);
    box-sizing: border-box;
    opacity: 0.9;
  }
  .scene-photo {
    position: absolute; left: 0; top: 366px; width: 356px; height: 335px;
    background:
      linear-gradient(180deg, rgba(255,255,255,1) 0%, rgba(255,255,255,0) 22%),
      linear-gradient(180deg, rgba(31,111,190,0) 55%, rgba(38,118,196,0.9) 78%, #1f6fbe 100%),
      linear-gradient(90deg, #9a9c9e 0%, #bdbfc1 22%, #d9dadb 45%, #eef0f2 65%, #e6e8ea 85%, #a9abad 100%);
  }
  .tagline-top {
    position: absolute; left: 27px; top: 16px; margin: 0;
    font-size: 11.5px; font-weight: 400; letter-spacing: 0.1px;
    color: var(--blue-title); white-space: nowrap;
  }
  .brand {
    position: absolute; left: 0; width: 356px; top: 80px;
    display: flex; flex-direction: column; align-items: center;
  }
  .brand-dot {
    width: 62px; height: 62px; border-radius: 50%;
    background: var(--blue-brand);
  }
  .brand-name {
    margin-top: 6px;
    font-size: 30px; font-weight: 700; color: #111111; line-height: 1;
  }
  .product-title {
    position: absolute; left: 26px; top: 221px; margin: 0;
    font-size: 58px; font-weight: 800; line-height: 48px;
    color: var(--blue-title); letter-spacing: -0.5px;
  }
  .product-claim {
    position: absolute; left: 33px; top: 328px; margin: 0;
    font-size: 20px; font-weight: 300; line-height: 18px;
    color: var(--navy-text);
  }
  .rule { position: absolute; height: 1px; background: rgba(255,255,255,0.85); }
  .rule-top { left: 32px; width: 287px; top: 565px; }
  .rule-bottom { left: 34px; width: 290px; top: 637px; }
  .divider { position: absolute; left: 99px; top: 573px; width: 1px; height: 52px; background: rgba(255,255,255,0.85); }
  .suitable-heading {
    position: absolute; left: 32px; top: 583px; margin: 0;
    font-size: 12.5px; font-weight: 600; line-height: 13px; color: var(--white); letter-spacing: -0.3px;
  }
  .usp {
    position: absolute; top: 578px; width: 70px; margin-left: -35px;
    display: flex; flex-direction: column; align-items: center;
    color: var(--white); font-size: 8.5px; font-weight: 400; letter-spacing: 0.2px;
  }
  .usp svg { width: 20px; height: 20px; margin-bottom: 6px; }
  .closing-line {
    position: absolute; left: 33px; top: 652px; margin: 0;
    font-size: 12px; font-weight: 300; line-height: 13px; color: var(--white);
  }
  .net-label {
    position: absolute; left: 244px; top: 650px; margin: 0;
    font-size: 9px; font-weight: 300; color: var(--white); line-height: 1;
  }
  .net-volume {
    position: absolute; left: 243px; top: 658px; margin: 0;
    font-size: 21px; font-weight: 700; color: var(--white); line-height: 1;
  }
</style>
</head>
<body>
  <div class="label">
    <div class="label-face">
      <div class="face-content">
        <div class="bg-ring"></div>
        <div class="scene-photo" role="img" aria-label="Photo of a bright modern bathroom with glass shower, washbasin, mirror and bathtub"></div>

        <p class="tagline-top">A READY-TO-USE PRODUCT FOR EVERYDAY USE.</p>

        <div class="brand">
          <div class="brand-dot"></div>
          <div class="brand-name">Vorlix</div>
        </div>

        <h1 class="product-title">Sanitary<br>Cleaner</h1>
        <p class="product-claim">&rarr; Cleans, Descales<br>&nbsp;&amp; Freshens</p>

        <div class="rule rule-top"></div>
        <p class="suitable-heading">SUITABLE<br>FOR:</p>
        <div class="divider"></div>

        <div class="usp" style="left:135px">
          <svg viewBox="0 0 24 24" fill="none" stroke="#fff" stroke-width="2"><path d="M12 2l8 3v6c0 5-3.5 9-8 11-4.5-2-8-6-8-11V5z"/><path d="M12 7l3 1.2v3c0 2.3-1.4 4-3 4.8-1.6-.8-3-2.5-3-4.8v-3z" fill="#fff"/></svg>
          <span>SANITARY</span>
        </div>
        <div class="usp" style="left:184px">
          <svg viewBox="0 0 24 24" fill="#fff"><rect x="13" y="2" width="6" height="9" rx="1"/><path d="M4 11h16c0 4-3 6-6 6l1 5H8l1-5c-3-1-5-3-5-6z"/></svg>
          <span>TOILET</span>
        </div>
        <div class="usp" style="left:236px">
          <svg viewBox="0 0 24 24" fill="none" stroke="#fff" stroke-width="1.6"><path d="M20 22V8a5 5 0 0 0-9-3"/><path d="M6 9l8-3-1 6z" fill="#fff"/><path d="M6 13l-2 5M9 14l-1 5M12 14l0 5M8 12l-4 3"/></svg>
          <span>BATHROOM</span>
        </div>
        <div class="usp" style="left:301px">
          <svg viewBox="0 0 24 24" fill="#fff"><path d="M14 3l2 6 6 2-6 2-2 6-2-6-6-2 6-2z"/><path d="M5 2l1 2.5L8.5 5 6 6 5 8.5 4 6 1.5 5 4 4z"/><path d="M6 16l.8 2 2 .8-2 .8L6 21.6l-.8-2-2-.8 2-.8z"/></svg>
          <span>WET AREAS</span>
        </div>

        <div class="rule rule-bottom"></div>
        <p class="closing-line">IDEAL FOR QUICK AND<br>POWERFUL CLEANING.</p>
        <p class="net-label">NET WT</p>
        <p class="net-volume">500ML</p>
      </div>
    </div>
  </div>
</body>
</html>
```